Calder Vane LED - E- Commerce site

We need a website designed for an LED Billboard company that sells:
1) LED Billboards (Sales & Rental)
2) LED Gas Station lights
3) Truss Systems (Sales & Rental)
4) Sound Systems (Sales & Rental)

Attached are websites that sell similar products as Calder Vane LED. Target market is for business, property managers and event coordinators.
This site will need to be an e-commerce site where customers can purchase the product directly from the site. What I'm looking for is a design layout to start.

Conceptual Web Designs:
http://192.0.2.47:8087/index.html
http://www.pmvdisplay.example/
http://www.auralomaaudio.example/
http://www.quillmarkpanel.example/

Attached is the logo of the company: Please note that the new spelling of the logo is "Calder Vane LED" using domain " CalderVaneLED.com

Industry/Entity Type

Gas Station

Number of Pages Required

5+ page

Requirements
Must have
• 1) E-Commerce - Customers will need to be able to order product from the site.
• 2) Customers will also have the option to rent the product as well.
Nice to have
• I like the image of the attached website, that has a video clip loop
• http://www.quillmarkpanel.example/

```html
<!DOCTYPE html>
<html lang="en">
<head>
<meta charset="utf-8">
<title>Calder Vane LED</title>
<link href="https://fonts.googleapis.com/css2?family=Audiowide&family=Lato:wght@400;700&display=swap" rel="stylesheet">
<style>
:root{
  --ink:#1b1a1d;
  --header:#141316;
  --navy:#23236b;
  --pink:#e6296e;
  --gold:#f2c11a;
  --red:#e0262e;
  --teal:#06a3c3;
  --text:#444;
  --white:#fff;
  --rule:#e7a0a8;
}
*{box-sizing:border-box;margin:0;padding:0}
html,body{width:1200px;height:2647px;overflow:hidden}
body{position:relative;background:var(--white);font-family:'Lato',sans-serif;color:var(--text)}
.abs{position:absolute}
/* header */
.site-header{left:0;top:0;width:1200px;height:60px;background:var(--header)}
.brand-small{left:78px;top:20px;font-family:'Audiowide',sans-serif;font-size:14px;color:var(--gold);display:flex;align-items:center;gap:7px;white-space:nowrap}
.brand-small i{width:14px;height:14px;border-radius:50%;background:var(--pink);display:block}
.main-nav{left:0;top:0;width:820px;height:60px;font-size:12.5px;color:#ddd;letter-spacing:.4px}
.main-nav span{position:absolute;top:22px;white-space:nowrap}
.main-nav .active{color:var(--pink)}
.main-nav .active::after{content:"";position:absolute;left:0;right:0;bottom:-8px;height:3px;background:var(--pink)}
.search{left:828px;top:12px;width:188px;height:30px;background:#2a292d;border:1px solid #3b3a3f;display:flex;align-items:center;justify-content:space-between;padding:0 10px;font-size:11px;color:#888;white-space:nowrap}
.cart{left:1030px;top:10px;width:88px;height:34px;background:#2a292d;display:flex;align-items:center;justify-content:center;gap:8px;color:#fff;font-size:14px}
/* hero */
.hero{left:0;top:60px;width:1200px;height:493px;background:linear-gradient(180deg,#2b2b35 0%,#1a1730 35%,#3a2450 55%,#131428 72%,#0a0c18 100%)}
.hero-brand{left:82px;top:200px;font-family:'Audiowide',sans-serif;color:var(--gold);display:flex;align-items:center;gap:18px}
.hero-brand i{width:44px;height:44px;border-radius:50%;background:var(--pink);display:block}
.hero-brand span{font-size:48px;line-height:1.1;white-space:nowrap}
.hero-tag{left:494px;top:208px;font-family:'Audiowide',sans-serif;color:#fff;font-size:28px;letter-spacing:1px;white-space:nowrap}
.hero-title{left:490px;top:250px;font-family:'Audiowide',sans-serif;color:var(--gold);font-size:94px;line-height:1;white-space:nowrap}
/* section titles */
.section-title{left:0;width:1200px;text-align:center;font-family:'Audiowide',sans-serif;font-size:28px;color:var(--navy);letter-spacing:1px}
.title-rule{left:287px;width:626px;height:2px;background:var(--rule)}
.title-rule::after{content:"";position:absolute;left:263px;width:100px;top:0;height:2px;background:var(--gold)}
/* products */
.product-card{top:688px;width:240px;height:293px;border:5px dashed #d9b6c4;padding:13px 11px;text-align:center}
.product-photo{width:208px;height:112px}
.product-card h3{font-size:15px;font-weight:700;color:#222;margin:16px 0 6px;letter-spacing:.3px;white-space:nowrap}
.product-card .line{height:2px;background:var(--pink);margin:0 4px 8px}
.product-card p{font-size:10.5px;line-height:16px;color:#555}
.actions{display:flex;justify-content:center;gap:14px;margin-top:18px}
.btn{font-size:9px;color:#fff;padding:4px 0;width:46px;display:block;letter-spacing:.5px}
.btn-buy{background:var(--red)}
.btn-rent{background:var(--ink)}
/* specialities */
.specialities{left:0;top:1036px;width:1200px;height:466px;background:var(--teal)}
.spec-icon{top:1156px;width:124px;height:124px}
.spec-card{top:1297px;width:240px;height:164px;background:#fff;text-align:center;padding:20px 8px 0}
.spec-card h3{font-size:17px;color:#222;letter-spacing:1px;font-weight:700;margin-bottom:10px}
.spec-card p{font-size:11.5px;line-height:21px;color:#555;white-space:nowrap}
.spec-card .more{font-size:10px;font-weight:700;color:#222;margin-top:6px}
/* featured */
.tile{position:absolute}
.tile-caption{left:18px;bottom:26px;width:244px;color:var(--gold);font-size:14.5px;line-height:23px;text-transform:uppercase}
/* newsletter */
.newsletter{left:0;top:2337px;width:988px;height:35px;background:var(--red);clip-path:polygon(0 0,96% 0,100% 100%,0 100%)}
.newsletter-label{left:79px;top:2347px;font-size:13px;color:#fff;letter-spacing:.5px}
.field{top:2343px;height:24px;background:#fff;font-size:9px;color:#999;padding:6px 6px}
.send{left:641px;top:2343px;width:86px;height:24px;background:var(--gold);font-size:10px;text-align:center;line-height:24px;color:#222}
.social{top:2340px;width:28px;height:28px}
/* footer */
.site-footer{left:0;top:2376px;width:1200px;height:233px;background:var(--ink)}
.foot-h{font-size:13.5px;color:var(--gold);letter-spacing:.5px;border-bottom:1px solid #555;padding-bottom:4px}
.quick-links li{list-style:none;font-size:11.5px;color:#ddd;border-bottom:1px solid #444;padding:4px 0}
.foot-text{font-size:11.5px;line-height:18px;color:#ddd;white-space:nowrap}
.closed{color:var(--red)}
.foot-brand{left:852px;top:2455px;font-family:'Audiowide',sans-serif;color:var(--gold);font-size:30px;display:flex;align-items:center;gap:12px}
.foot-brand i{width:30px;height:30px;border-radius:50%;background:var(--pink);display:block}
.bottom-bar{left:0;top:2609px;width:1200px;height:38px;background:#0d0c0f;font-size:10.5px;color:#aaa}
.bottom-bar span{white-space:nowrap}
</style>
</head>
<body>

<header class="abs site-header"></header>
<div class="abs brand-small"><i></i>Calder Vane LED</div>
<nav class="abs main-nav">
  <span class="active" style="left:244px">HOME</span>
  <span style="left:318px">ABOUT US</span>
  <span style="left:417px">LED DISPLAYS</span>
  <span style="left:538px">SOLUTION</span>
  <span style="left:637px">GALLERY</span>
  <span style="left:725px">CONTACT US</span>
</nav>
<div class="abs search">Enter your Key words
  <svg width="14" height="14" viewBox="0 0 14 14"><circle cx="6" cy="6" r="4.5" fill="none" stroke="#fff" stroke-width="2"/><line x1="9.3" y1="9.3" x2="13" y2="13" stroke="#fff" stroke-width="2.2"/></svg>
</div>
<div class="abs cart">
  <svg width="24" height="20" viewBox="0 0 24 20"><path d="M1 2h4l3 11h12l2-8H7" fill="none" stroke="#fff" stroke-width="1.8"/><circle cx="10" cy="17" r="1.8" fill="#fff"/><circle cx="18" cy="17" r="1.8" fill="#fff"/></svg>(01)
</div>

<section class="abs hero" role="img" aria-label="Night city skyline with lit towers reflected on a harbour"></section>
<div class="abs hero-brand"><i></i><span>Calder Vane<br>LED</span></div>
<div class="abs hero-tag">WE HAVE THE POWER TO ENLIGHTEN</div>
<div class="abs hero-title">THE WORLD</div>

<h2 class="abs section-title" style="top:598px">OUR PRODUCTS</h2>
<div class="abs title-rule" style="top:641px"></div>

<article class="abs product-card" style="left:79px">
  <div class="product-photo" role="img" aria-label="LED billboards on city buildings at night" style="background:linear-gradient(135deg,#1c1c22,#5a5660 50%,#25232a)"></div>
  <h3>LED BILLBOARDS</h3><div class="line"></div>
  <p>Lorem Ipsum is simply dummy text of the printing and typesetting industry. Lorem specimen book was popularised .</p>
  <div class="actions"><span class="btn btn-buy">BUY</span><span class="btn btn-rent">RENTAL</span></div>
</article>
<article class="abs product-card" style="left:348px">
  <div class="product-photo" role="img" aria-label="Garden lamp standing on green grass" style="background:linear-gradient(160deg,#6f8f3a,#3e6422 60%,#2c4a19)"></div>
  <h3>LED GAS STATION LIGHTS</h3><div class="line"></div>
  <p>Lorem Ipsum is simply dummy text of the printing and typesetting industry. Lorem specimen book was popularised .</p>
  <div class="actions"><span class="btn btn-buy">BUY</span><span class="btn btn-rent">RENTAL</span></div>
</article>
<article class="abs product-card" style="left:616px">
  <div class="product-photo" role="img" aria-label="Worker assembling a metal truss structure" style="background:linear-gradient(160deg,#9aa3ab,#6d6f72 60%,#4a4b4d)"></div>
  <h3>TRUSS SYSTEMS</h3><div class="line"></div>
  <p>Lorem Ipsum is simply dummy text of the printing and typesetting industry. Lorem specimen book was popularised .</p>
  <div class="actions"><span class="btn btn-buy">BUY</span><span class="btn btn-rent">RENTAL</span></div>
</article>
<article class="abs product-card" style="left:884px">
  <div class="product-photo" role="img" aria-label="Sound mixing desk and speakers" style="background:linear-gradient(160deg,#4a4a4e,#222225 60%,#111)"></div>
  <h3>SOUND SYSTEMS</h3><div class="line"></div>
  <p>Lorem Ipsum is simply dummy text of the printing and typesetting industry. Lorem specimen book was popularised .</p>
  <div class="actions"><span class="btn btn-buy">BUY</span><span class="btn btn-rent">RENTAL</span></div>
</article>

<section class="abs specialities"></section>
<h2 class="abs section-title" style="top:1080px;color:#fff">OUR SPECIALITIES</h2>
<div class="abs title-rule" style="top:1124px;background:#2a6f86"></div>

<svg class="abs spec-icon" style="left:137px" viewBox="0 0 124 124"><circle cx="62" cy="62" r="60" fill="var(--teal)" stroke="#fff" stroke-width="3"/><circle cx="62" cy="62" r="50" fill="none" stroke="#fff" stroke-width="1"/><circle cx="55" cy="68" r="15" fill="none" stroke="var(--gold)" stroke-width="9" stroke-dasharray="6 4"/><circle cx="55" cy="68" r="6" fill="var(--gold)"/><circle cx="78" cy="46" r="9" fill="none" stroke="var(--gold)" stroke-width="6" stroke-dasharray="4 3"/></svg>
<svg class="abs spec-icon" style="left:405px" viewBox="0 0 124 124"><circle cx="62" cy="62" r="60" fill="var(--teal)" stroke="#fff" stroke-width="3"/><circle cx="62" cy="62" r="50" fill="none" stroke="#fff" stroke-width="1"/><path d="M62 32l24 9v18c0 16-10 27-24 33-14-6-24-17-24-33V41z" fill="var(--gold)"/></svg>
<svg class="abs spec-icon" style="left:673px" viewBox="0 0 124 124"><circle cx="62" cy="62" r="60" fill="var(--teal)" stroke="#fff" stroke-width="3"/><circle cx="62" cy="62" r="50" fill="none" stroke="#fff" stroke-width="1"/><path d="M38 66V58a24 24 0 0 1 48 0v8" fill="none" stroke="var(--gold)" stroke-width="5"/><rect x="32" y="58" width="11" height="18" rx="4" fill="var(--gold)"/><rect x="81" y="58" width="11" height="18" rx="4" fill="var(--gold)"/><path d="M86 76q0 12-18 12" fill="none" stroke="var(--gold)" stroke-width="3"/></svg>
<svg class="abs spec-icon" style="left:941px" viewBox="0 0 124 124"><circle cx="62" cy="62" r="60" fill="var(--teal)" stroke="#fff" stroke-width="3"/><circle cx="62" cy="62" r="50" fill="none" stroke="#fff" stroke-width="1"/><circle cx="62" cy="62" r="26" fill="none" stroke="var(--gold)" stroke-width="7" stroke-dasharray="9 3"/><path d="M50 62l9 9 16-17" fill="none" stroke="var(--gold)" stroke-width="5"/></svg>

<article class="abs spec-card" style="left:79px"><h3>TECHNOLOGY</h3><p>Lorem Ipsum is simply dummy text of<br>the printing and typesetting the<br>unknown printer took.</p><div class="more">READ MORE...</div></article>
<article class="abs spec-card" style="left:348px"><h3>WARRANTY</h3><p>Lorem Ipsum is simply dummy text of<br>the printing and typesetting the<br>unknown printer took.</p><div class="more">READ MORE...</div></article>
<article class="abs spec-card" style="left:616px"><h3>SERVICE</h3><p>Lorem Ipsum is simply dummy text of<br>the printing and typesetting the<br>unknown printer took.</p><div class="more">READ MORE...</div></article>
<article class="abs spec-card" style="left:884px"><h3>QUALITY</h3><p>Lorem Ipsum is simply dummy text of<br>the printing and typesetting the<br>unknown printer took.</p><div class="more">READ MORE...</div></article>

<h2 class="abs section-title" style="top:1537px">FEATURED PRODUCTS</h2>
<div class="abs title-rule" style="top:1580px"></div>

<div class="tile" role="img" aria-label="Lit cable bridge over water at dusk" style="left:164px;top:1631px;width:583px;height:305px;background:linear-gradient(180deg,#3b3160 0%,#4b3a6e 45%,#1c1b2e 70%,#0e0e16 100%)"></div>
<div class="tile" role="img" aria-label="LED bulbs with cooling chips" style="left:768px;top:1631px;width:280px;height:305px;background:linear-gradient(160deg,#6a6a66,#4a4a47 55%,#333)">
  <div class="abs tile-caption">Various LEDs bulb GU10 and<br>E27 with different<br>cooling SMD chips</div>
</div>
<div class="tile" role="img" aria-label="Glowing LED lamp in warm light" style="left:164px;top:1961px;width:277px;height:305px;background:radial-gradient(circle at 45% 45%,#f0a050,#b0402a 45%,#3a1020 80%)"></div>
<div class="tile" role="img" aria-label="White interior with pendant bulbs and wooden floor" style="left:464px;top:1961px;width:276px;height:305px;background:linear-gradient(180deg,#ececea 0%,#dcdad6 60%,#6b4d36 78%,#4d3625 100%)"></div>
<div class="tile" role="img" aria-label="Floodlit stadium at night" style="left:768px;top:1961px;width:280px;height:305px;background:linear-gradient(180deg,#0c2a44 0%,#1c4a6e 45%,#2b6b3c 75%,#1e4f2c 100%)"></div>

<div class="abs newsletter"></div>
<div class="abs newsletter-label">NEWSLETTER</div>
<div class="abs field" style="left:175px;width:216px">Name</div>
<div class="abs field" style="left:408px;width:216px">Email ID</div>
<div class="abs send">SEND</div>
<div class="abs social" style="left:1015px;background:#3b5a9a"></div>
<div class="abs social" style="left:1053px;background:#cc1f2a"></div>
<div class="abs social" style="left:1091px;background:#3a3a3a"></div>

<footer class="abs site-footer"></footer>
<div class="abs" style="left:79px;top:2402px;width:164px">
  <div class="foot-h">QUICK LINKS</div>
  <ul class="quick-links"><li>Home</li><li>About Us</li><li>LED Displays</li><li>Solution</li><li>Gallery</li><li>Contact us</li></ul>
</div>
<div class="abs" style="left:292px;top:2402px;width:226px">
  <div class="foot-h">SHOWROOM</div>
  <p class="foot-text" style="margin-top:5px">gddgdgshg bdddhd<br>Marel gate 41<br>0190 Harbourtown</p>
  <div class="foot-h" style="margin-top:10px">OPENING HOURS</div>
  <p class="foot-text" style="margin-top:5px">Monday to Friday: 10:00 to 18:00<br>Saturday: 11:00 to 16:00<br><span class="closed">Sunday closed</span></p>
</div>
<div class="abs" style="left:570px;top:2402px;width:222px">
  <div class="foot-h">ADDRESS</div>
  <p class="foot-text" style="margin-top:5px">svfsfsf vdsgbshgsd ndhndjndf<br>Tel: +123 555 0190<br>Email: post@caldervaneled.example</p>
</div>
<div class="abs foot-brand"><i></i>Calder Vane<br>LED</div>

<div class="abs bottom-bar">
  <span class="abs" style="left:79px;top:13px">Copyright caldervaneled. All rights reserved.</span>
  <span class="abs" style="left:900px;top:13px">Terms &amp; Conditions &nbsp;&nbsp;|&nbsp;&nbsp; Delivery conditions</span>
</div>

</body>
</html>
```